Private Investment Firm Needs PowerPoint Presentation Template

Design PowerPoint template, take Pinebrook-submitted rough presentation draft, and drop it into new template. See attached Project Brief file for more detail.
Updates

Some decent designs have been submitted but they seem to lack the understanding of our target markets. I am hopeful that more time and feedback will result in better results.

Target Market(s)

Private company owners and intermediaries.

Font styles to use
Serif

Colors
3176b5

Requirements
Must have
• See attached Project Brief.
Nice to have
Should not have
• No B2C fluff--this is a B2B project.

```html
<!DOCTYPE html>
<html lang="en">
<head>
<meta charset="utf-8">
<title>Pinebrook Capital – Client Perspective</title>
<link rel="stylesheet" href="https://fonts.googleapis.com/css2?family=Figtree:wght@400;700&family=Tinos:wght@400&display=swap">
<style>
  :root {
    --brand-blue: #0a6ebd;
    --paper: #ffffff;
    --ink-white: #ffffff;
    --fog-light: #c9d3da;
    --fog-mid: #8e9ca7;
    --fog-dark: #4d5d6b;
  }
  html, body {
    margin: 0;
    padding: 0;
    overflow: hidden;
    background: var(--paper);
  }
  .slide {
    position: relative;
    width: 1200px;
    height: 676px;
    overflow: hidden;
    background: var(--paper);
  }
  .side-band {
    position: absolute;
    top: 0;
    left: 0;
    width: 44px;
    height: 676px;
    background: var(--brand-blue);
  }
  .edge-band {
    position: absolute;
    top: 0;
    right: 0;
    width: 10px;
    height: 676px;
    background: var(--brand-blue);
  }
  .site-address {
    position: absolute;
    left: 22px;
    top: 338px;
    transform: translate(-50%, -50%) rotate(-90deg);
    white-space: nowrap;
    font-family: "Tinos", serif;
    font-size: 15px;
    letter-spacing: 0.3px;
    color: var(--ink-white);
  }
  .page-number {
    position: absolute;
    top: 18px;
    left: 1157px;
    font-family: "Tinos", serif;
    font-size: 18px;
    color: #333;
  }
  .hero-photo {
    position: absolute;
    left: 269px;
    top: 48px;
    width: 869px;
    height: 579px;
    background:
      radial-gradient(ellipse at 72% 40%, rgba(190, 90, 70, 0.35), transparent 45%),
      linear-gradient(160deg, var(--fog-light) 0%, var(--fog-mid) 55%, var(--fog-dark) 100%);
  }
  .quote-card {
    position: absolute;
    left: 110px;
    top: 83px;
    width: 652px;
    height: 300px;
    box-sizing: border-box;
    padding: 38px 40px 0 34px;
    background: var(--brand-blue);
    color: var(--ink-white);
    font-family: "Figtree", sans-serif;
  }
  .quote-text {
    margin: 0;
    font-size: 17.6px;
    font-weight: 700;
    line-height: 28px;
    letter-spacing: 0.2px;
  }
  .quote-source {
    margin: 26px 0 0;
    font-size: 17.6px;
    font-weight: 400;
    letter-spacing: 0.2px;
  }
  .brand-mark {
    position: absolute;
    left: 67px;
    top: 612px;
    display: flex;
    align-items: center;
    gap: 10px;
    font-family: "Tinos", serif;
    font-size: 20px;
    letter-spacing: 1.5px;
    color: var(--brand-blue);
  }
  .brand-dot {
    width: 34px;
    height: 34px;
    border-radius: 50%;
    background: var(--brand-blue);
  }
</style>
</head>
<body>
<main class="slide">
  <div class="side-band"></div>
  <div class="site-address">www.pinebrookcapital.com</div>
  <div class="edge-band"></div>
  <div class="page-number">5</div>

  <div class="hero-photo" role="img" aria-label="Photograph of a red suspension bridge tower rising through thick grey fog"></div>

  <section class="quote-card">
    <p class="quote-text">“Our company had several business opportunities but I<br>needed outside capital to take advantage of them. Why would<br>I cede control of my business when we were at the exact<br>point when raising outside capital would allow me to acceler-<br>ate growth and achieve my life-long business and personal<br>goals?!”</p>
    <p class="quote-source">-Daniel Porter, CEO; The Harlow Group</p>
  </section>

  <div class="brand-mark">
    <span class="brand-dot"></span>
    <span class="brand-name">PINEBROOK CAPITAL</span>
  </div>
</main>
</body>
</html>
```